Mortgage Company ready to make a statement!

We have a basic logo that I am fairly happy with ... but it could use a little bit of tweaking before we order the sign for our building. We also want some knock-your-socks-off business cards.
Problem: Inside of our Mortgage Office (Bright Fern Mortgage Group), we are going to have a coffee lounge (Sunbrew Cafe) for Realtors to use instead of the local Cuppington to meet with homebuyers. The office and coffee lounge are in an industrial building and is decorated with cozy overstuffed chairs, a hodge podge of interesting lamps and furniture, and goal is to make it as inviting as possible. However, we are a financial institution... so we need to keep it pretty clean as well.
One of my favorite marketing ideas is to cut a house key for everyone who buys a home using us with a key that matches our logo. There's only one key shape that works really well, so that needs to match the logo in order for the idea to work. I'll attach an image of the key blank.... although the way the key hole cut out looks terrible, so I was thinking of having them just do a thin outline instead.
Would like a similar, matching logo for the Sunbrew Cafe... but possibly something that would be a little less formal and would be cute on a coffee mug- nothing stuffy.
AND, we're opening a home inspection company as well, and we would like that logo and branding to match. The home inspection company is "Bright Fern Home Inspections"
We were thinking that for the home inspection company , we could use a magnifying glass shape inside of the house shape for the logo, use a keyhole shape inside of the same house for the mortgage company, and use a coffee cup inside of the house shape for Sunbrew Cafe.
Just getting stuck and need to help. I designed the attached logo myself, and that is what we are currently using. Designers at local printing companies have failed to impress us.
The mortgage industry has a lot of numbers and logos, etc that they require us to put on our business cards... so it's hard to keep them looking clean.
HELP! HELP! :)

```html
<!DOCTYPE html>
<html lang="en">
<head>
<meta charset="utf-8">
<title>Bright Fern Mortgage Group – Business Cards</title>
<link rel="stylesheet" href="https://fonts.googleapis.com/css2?family=Marcellus&family=Montserrat:wght@400;600&display=swap">
<style>
  :root{
    --bg:#efede8;
    --card:#ffffff;
    --brand-blue:#1f6285;
    --ink-grey:#4a4852;
    --text-grey:#55545c;
    --shadow:rgba(40,40,50,.28);
  }
  *{box-sizing:border-box;margin:0;padding:0}
  html,body{width:1200px;height:929px;overflow:hidden}
  body{background:var(--bg);position:relative;font-family:"Montserrat",sans-serif}

  .card{
    position:absolute;width:520px;height:297px;background:var(--card);
    box-shadow:4px 6px 10px var(--shadow);overflow:hidden;
  }
  .card--front{left:50px;top:316px}
  .card--back{left:630px;top:316px}

  /* front */
  .brand{
    position:absolute;inset:0;display:flex;align-items:center;justify-content:center;gap:16px;
  }
  .brand__dot{width:34px;height:34px;border-radius:50%;background:var(--brand-blue)}
  .brand__name{
    font-family:"Marcellus",serif;font-size:30px;color:var(--brand-blue);letter-spacing:.5px;
  }

  /* back */
  .back__mark{
    position:absolute;left:58px;top:78px;width:150px;text-align:center;
  }
  .back__circle{width:96px;height:96px;border-radius:50%;background:var(--brand-blue);margin:0 auto 12px}
  .back__name{font-family:"Marcellus",serif;font-size:17px;color:var(--brand-blue);line-height:1.2}

  .back__rule{position:absolute;left:258px;top:56px;width:1.5px;height:142px;background:var(--brand-blue)}

  .contact{position:absolute;left:276px;top:54px;color:var(--text-grey)}
  .contact__name{font-family:"Marcellus",serif;font-size:23px;color:var(--brand-blue);letter-spacing:.5px}
  .contact__title{font-weight:600;font-size:14px;color:var(--ink-grey);margin:2px 0 12px}
  .contact__address{font-size:11.5px;line-height:1.35;letter-spacing:.4px;margin-bottom:10px}
  .contact__line{display:flex;align-items:center;gap:8px;font-size:11.5px;letter-spacing:.4px;line-height:1.6}
  .contact__icon{width:11px;height:11px;flex:none}

  .swoosh{position:absolute;left:0;bottom:0;width:520px;height:70px}
</style>
</head>
<body>

<section class="card card--front" aria-label="Card front">
  <div class="brand">
    <span class="brand__dot"></span>
    <span class="brand__name">Bright Fern Mortgage Group</span>
  </div>
</section>

<section class="card card--back" aria-label="Card back">
  <div class="back__mark">
    <div class="back__circle"></div>
    <div class="back__name">Bright Fern<br>Mortgage Group</div>
  </div>

  <div class="back__rule"></div>

  <div class="contact">
    <p class="contact__name">DANA WHITLOW</p>
    <p class="contact__title">CEO</p>
    <p class="contact__address">Harbour Court<br>Eastvale City</p>
    <p class="contact__line">
      <svg class="contact__icon" viewBox="0 0 12 12"><rect x="3" y="0.8" width="6" height="10.4" rx="1" fill="none" stroke="#4a4852" stroke-width="1.2"/><circle cx="6" cy="9.3" r=".7" fill="#4a4852"/></svg>
      000-555-0142
    </p>
    <p class="contact__line">
      <svg class="contact__icon" viewBox="0 0 12 12"><rect x="3" y="0.5" width="6" height="3.5" fill="#4a4852"/><rect x="0.5" y="4.5" width="11" height="4.5" rx="1" fill="#4a4852"/><rect x="3" y="8" width="6" height="3.5" fill="#fff" stroke="#4a4852"/></svg>
      000-555-0187
    </p>
    <p class="contact__line">
      <svg class="contact__icon" viewBox="0 0 12 12"><rect x="0.5" y="2.5" width="11" height="7.5" fill="#1f6285"/><path d="M0.8 2.8 L6 7 L11.2 2.8" fill="none" stroke="#fff" stroke-width="1"/></svg>
      dana.whitlow@brightfernmg.com
    </p>
  </div>

  <svg class="swoosh" viewBox="0 0 520 70" preserveAspectRatio="none" aria-hidden="true">
    <path d="M0 70 L0 64 C150 60 330 40 520 0 L520 70 Z" fill="#1f6285"/>
    <path d="M0 64 C150 60 330 40 520 0 L520 12 C330 50 150 66 0 70 Z" fill="#ffffff"/>
  </svg>
</section>

</body>
</html>
```